Marigold Synchronized Swim Team's Clubhouse (web page)

Fun, Super Easy to read and navigate. Please error on the side of too large font sizes rather than too small font sizes.

We are a New Orleans (USA) based club for adults and youth of all genders.

We have youth and adult performance and competition teams. We teach synchronized swimming. We perform at special events.

Webpage should allow for

1. Sign up for classes, camps and teams (pay fees, sign waivers, reserve a spot and link to national Delmar Aquaform club membership website in order to buy required national membership).Make our multi step registration process easy, quick, pleasant.

2. Provide an area to upload practice schedules.
and performance calendar.

3. Easily
Hire one of our synchro squad to perform at special events.

4. Embedded Google Calndar

5 Members only site
( one away for youth and one area for adults. )

6 Show off our new logo, photos and videos. Be able to change these images often.

Our team colors are red, aqua and pink.

7. Buy logo gear

Click to team shop at
Brindle cove.com and other future team shops.

8. One click to become a sponsor of the team.

An area to show off sponsor logos. We will have several levels of sponsorships. It is important to have small medium and large logo spots. WE also will have a wall of names of folks who donate 10 - 100 dollars to sponsor the team.

We want the experience to be fun . We do not want headache producing events.

Our team colors are red, pink and aqua. WE have not settled on a specific red or pink yet. You are free to play around with different tones and hues. I tend toward a sholcking pink and cherry red. But really do want to see what your thoughts are for our reds and pinks. Also feel free to vary aqua from a light to dark. But we do want to stay away from navy.
Thanks for your hard work and creativity.

Target Market(s)

All ages, genders and ethnicity. Swimmers, dancers and event planners.

Coding

Coded - Design and coding required

Number of Pages Required

4 page

Font styles to use
Sans Serif

Colors
ec1f27
0293ce
f59195

Requirements
Must have
• See p descriptions +
• Fine #20 is our logo and
• Playful, bold, elegant, Colorful (red, aqua and pink are our team colors).
• I want to be able to plug in / update photos , schedules, release forms, almost everything as our seasons change. I do not know ( Newbury) do I want coded or incised site. All advice welcome.
Nice to have
• Your flare as a designer. Thank you for making us better through your creativity, ability to edit, clarify and advice. :-)
Should not have
• Confusion.

```html
<!DOCTYPE html>
<html lang="en">
<head>
<meta charset="utf-8">
<title>Marigold Synchronized Swim Team — Clubhouse</title>
<link href="https://fonts.googleapis.com/css2?family=Audiowide&family=Open+Sans:wght@400;600;700&display=swap" rel="stylesheet">
<style>
:root{
  --red:#ec1f27;
  --aqua:#0293ce;
  --pink:#f59195;
  --ink:#222;
  --text:#555;
  --muted:#888;
  --line:#dcdcdc;
  --soft:#f1f1f1;
  --footer:#0a6ea3;
  --footer-deep:#075a87;
  --pool-a:#2aa7b8;
  --pool-b:#0e6f8f;
}
*{box-sizing:border-box;margin:0;padding:0}
html,body{width:1200px;height:3516px;overflow:hidden}
body{position:relative;background:#fff;font-family:"Open Sans",Arial,sans-serif;color:var(--text)}
.abs{position:absolute}
.heading{font-family:"Audiowide","Open Sans",sans-serif;color:var(--ink);font-size:28px;letter-spacing:2px;font-weight:400}
.photo{background:linear-gradient(135deg,var(--pool-a),var(--pool-b))}

/* header */
.topline{left:0;top:0;width:1200px;height:4px;background:var(--aqua)}
.header{left:0;top:4px;width:1200px;height:94px;background:rgba(255,255,255,.9);z-index:2}
.contact-bar{right:73px;top:14px;display:flex;gap:18px;align-items:center;font-size:14px;color:var(--ink)}
.contact-bar span{display:flex;align-items:center;gap:8px}
.dot-icon{width:22px;height:22px;border-radius:50%;background:var(--red);display:inline-flex;align-items:center;justify-content:center}
.signup-btn{border:2px solid var(--red);color:var(--red);font-weight:700;font-size:13px;padding:4px 10px;border-radius:3px}
.nav{left:380px;top:60px;display:flex;gap:26px;font-size:14px;font-weight:700;color:var(--ink)}
.nav .active{color:var(--red);border-bottom:2px solid var(--red);padding-bottom:3px}
.search{left:1084px;top:60px}
.logo-disc{left:70px;top:0;width:188px;height:178px;border-radius:0 0 94px 94px;background:#fff;z-index:3;display:flex;align-items:center;justify-content:center;flex-direction:column;gap:6px}
.logo-name{font-family:"Open Sans",sans-serif;font-weight:700;font-size:22px;color:var(--aqua)}
.logo-mark{width:36px;height:36px;border-radius:50%;background:var(--pink)}

/* hero */
.hero{left:0;top:0;width:1200px;height:600px;background:linear-gradient(160deg,#3fa9c2 0%,#1a7c9c 55%,#0d5f80 100%)}
.hero-title{left:0;top:215px;width:1200px;text-align:center;font-family:"Audiowide",sans-serif;font-size:92px;color:#fff;letter-spacing:6px}
.hero-arrow{top:308px;width:40px;height:40px;border-radius:50%;background:rgba(0,0,0,.35);display:flex;align-items:center;justify-content:center}
.hero-wave{left:0;top:470px}
.hero-strip{left:0;top:600px;width:1200px;height:96px;background:#fff}
.hero-lead{left:98px;top:610px;width:680px;font-size:21px;line-height:30px;color:var(--ink);font-weight:600}
.upload-btn{left:800px;top:618px;width:300px;height:48px;border:2px solid var(--red);border-radius:3px;color:var(--red);font-weight:700;font-size:14px;display:flex;align-items:center;justify-content:center;gap:10px}

/* registration steps */
.steps{left:0;top:696px;width:1200px;height:510px;background:var(--soft)}
.steps .heading{position:absolute;left:0;top:48px;width:1200px;text-align:center}
.steps-intro{position:absolute;left:160px;top:104px;width:880px;text-align:center;font-size:13px;line-height:20px;color:var(--muted)}
.step{position:absolute;top:197px;width:230px;text-align:center}
.step-ring{width:146px;height:146px;margin:0 auto;border-radius:50%;border:2px solid #c9c9c9;background:#fff;display:flex;align-items:center;justify-content:center}
.step-name{margin-top:22px;font-size:20px;color:var(--ink);font-weight:600}
.step-text{margin-top:8px;font-size:13px;line-height:19px;color:var(--muted)}
.step-arrow{position:absolute;top:245px}
.divider{left:98px;width:1004px;height:1px;background:var(--line)}

/* events */
.events-title{left:98px;top:1250px}
.event{left:98px;width:605px;height:227px;border-bottom:1px solid var(--line);display:flex;gap:30px;padding-top:0}
.event-photo{width:232px;height:185px;flex:none;border:3px solid #e9e9e9}
.event-body{padding-top:6px}
.event-title{font-size:17px;font-weight:700;color:var(--ink)}
.meta{margin-top:8px;font-size:12px;color:var(--muted);display:flex;gap:8px;align-items:center}
.meta i{display:inline-block;width:10px;height:10px;background:var(--aqua);border-radius:2px}
.event-text{margin-top:10px;font-size:13px;line-height:20px;color:var(--text)}
.more{font-size:13px;font-weight:700;color:var(--red)}

/* calendar */
.cal-title{left:764px;top:1250px}
.calendar{left:778px;top:1315px;width:314px;height:326px;background:#fff;border:1px solid var(--line);padding:4px}
.cal-head{height:40px;background:var(--aqua);color:#fff;font-weight:700;font-size:16px;display:flex;align-items:center;justify-content:space-between;padding:0 14px}
.cal-grid{display:grid;grid-template-columns:repeat(7,1fr);gap:4px;padding:6px 2px}
.cal-grid b{text-align:center;font-size:15px;color:var(--ink);line-height:30px}
.cal-grid span{height:38px;background:#e3e3e3;border:1px solid #cfcfcf;display:flex;align-items:center;justify-content:center;font-size:15px;color:var(--ink)}
.cal-grid .empty{background:none;border:none}
.cal-grid .today{background:var(--red);color:#fff;border-color:var(--red)}

/* news */
.news-title{left:764px;top:1682px}
.news-item{left:764px;width:338px;height:99px;border-bottom:1px solid var(--line);display:flex;gap:16px;padding-top:0}
.news-thumb{width:108px;height:72px;flex:none}
.news-name{font-size:15px;font-weight:700;color:var(--ink)}

/* video */
.video-title{left:764px;top:2198px}
.video{left:764px;top:2257px;width:338px;height:188px;border:3px solid #e3e3e3;display:flex;align-items:center;justify-content:center}
.play{width:52px;height:52px;border-radius:50%;background:rgba(0,0,0,.65);display:flex;align-items:center;justify-content:center}

/* photos & feed */
.photos-title{left:98px;top:2545px}
.photo-grid{left:98px;top:2602px;width:605px;height:272px;display:grid;grid-template-columns:repeat(4,1fr);grid-template-rows:repeat(2,1fr);gap:6px}
.feed-title{left:741px;top:2545px}
.feed{left:741px;top:2602px;width:361px;height:272px;border:1px solid var(--line);background:#fff}
.feed-cover{height:140px;background:linear-gradient(135deg,#41b3c9,#13789a);position:relative}
.feed-avatar{position:absolute;left:12px;top:14px;width:44px;height:44px;background:#fff;border:2px solid #fff}
.feed-name{position:absolute;left:66px;top:16px;color:#fff;font-weight:700;font-size:15px}
.feed-sub{position:absolute;left:66px;top:38px;color:#fff;font-size:12px}
.feed-btn{position:absolute;bottom:10px;background:#f5f6f7;border:1px solid #ccd0d5;font-size:12px;font-weight:700;color:#4b4f56;padding:4px 10px;border-radius:2px}
.feed-note{padding:14px 12px 8px;font-size:12px;color:var(--muted)}
.feed-faces{display:flex;gap:6px;padding:0 12px}
.feed-faces span{width:40px;height:40px;background:linear-gradient(135deg,#c9a08c,#7f6a60)}

/* sponsors */
.sponsors{left:0;top:2930px;width:1200px;height:260px;background:#ececec}
.sponsors .heading{position:absolute;left:0;top:56px;width:1200px;text-align:center}
.sponsor-row{position:absolute;left:124px;top:105px;display:flex;gap:20px}
.sponsor{width:172px;height:78px;background:#fff;border:1px solid #d4d4d4;display:flex;align-items:center;justify-content:center}
.sponsor i{display:block;width:110px;height:30px;background:#bdbdbd;border-radius:4px}
.sponsor-arrow{top:135px}

/* footer */
.footer-wave{left:0;top:3140px}
.footer{left:0;top:3190px;width:1200px;height:326px;background:var(--footer);color:#e4f3fb}
.f-col{position:absolute;top:36px}
.f-col h4{font-size:18px;font-weight:600;color:#fff;margin-bottom:14px}
.f-col li{list-style:none;font-size:13px;line-height:23px}
.f-contact{display:flex;gap:12px;font-size:13px;line-height:21px;margin-bottom:16px}
.subscribe{display:flex;margin-top:12px}
.subscribe span{width:230px;height:36px;background:#fff;color:#999;font-size:12px;padding:9px 12px}
.subscribe b{width:94px;height:36px;background:var(--red);color:#fff;font-size:12px;display:flex;align-items:center;justify-content:center}
.socials{display:flex;gap:6px;margin-top:12px}
.socials span{width:32px;height:32px;border-radius:50%;border:2px solid rgba(255,255,255,.7)}
.copyright{position:absolute;left:0;top:276px;width:1200px;border-top:1px solid rgba(255,255,255,.2);padding-top:14px;text-align:center;font-size:12px;color:#cde8f6}

/* modal */
.dim{left:0;top:0;width:1200px;height:3516px;background:rgba(0,0,0,.24);z-index:10}
.modal{left:307px;top:227px;width:584px;height:387px;background:#fff;border:3px solid var(--aqua);z-index:11;text-align:center}
.modal-close{position:absolute;right:-26px;top:-26px;width:50px;height:50px;border-radius:50%;background:var(--aqua);border:3px solid #fff;color:#fff;font-size:24px;font-weight:700;display:flex;align-items:center;justify-content:center}
.modal-brand{margin-top:26px;display:flex;flex-direction:column;align-items:center;gap:4px}
.modal-brand .logo-mark{width:34px;height:34px}
.modal-title{margin-top:26px;font-family:"Audiowide",sans-serif;font-size:30px;color:var(--ink);letter-spacing:1px}
.modal-text{margin:18px auto 0;width:470px;font-size:13px;line-height:20px;color:var(--text)}
.modal-actions{position:absolute;left:60px;top:295px;display:flex;gap:18px}
.modal-actions span{width:223px;height:44px;display:flex;align-items:center;justify-content:center;font-weight:700;font-size:14px;border-radius:3px}
.btn-youth{background:var(--red);color:#fff}
.btn-adult{border:2px solid #999;color:var(--red)}
</style>
</head>
<body>

<!-- hero -->
<div class="abs hero" role="img" aria-label="Synchronized swimmer gliding through pool water"></div>
<div class="abs hero-title">MARIGOLDS</div>
<div class="abs hero-arrow" style="left:32px"><svg width="14" height="14" viewBox="0 0 14 14"><path d="M9 2 4 7l5 5" stroke="#fff" stroke-width="2" fill="none"/></svg></div>
<div class="abs hero-arrow" style="left:1126px"><svg width="14" height="14" viewBox="0 0 14 14"><path d="M5 2l5 5-5 5" stroke="#fff" stroke-width="2" fill="none"/></svg></div>
<svg class="abs hero-wave" width="1200" height="132" viewBox="0 0 1200 132"><path d="M0 60 C300 130 700 10 1200 70 L1200 132 L0 132Z" fill="#1da3d9" opacity=".8"/><path d="M0 90 C320 150 720 40 1200 100 L1200 132 L0 132Z" fill="#fff"/></svg>
<div class="abs hero-strip"></div>
<p class="abs hero-lead">At vero eos et accusamus et iusto odio dignissimos ducimus qui blanditiis praesentium voluptatum deleniti</p>
<div class="abs upload-btn"><svg width="16" height="16" viewBox="0 0 16 16"><rect x="1" y="1" width="14" height="14" rx="2" fill="var(--red)"/><path d="M8 4v7M5 7l3-3 3 3" stroke="#fff" stroke-width="1.6" fill="none"/></svg>UPLOAD AN PRACTICE SCHEDULES</div>

<!-- header -->
<div class="abs topline"></div>
<header class="abs header">
  <div class="abs contact-bar">
    <span><i class="dot-icon"><svg width="11" height="11" viewBox="0 0 12 12"><path d="M2 1h3l1 3-2 1a7 7 0 0 0 3 3l1-2 3 1v3c-6 0-10-4-9-9z" fill="#fff"/></svg></i>1 888 888 8888</span>
    <span><i class="dot-icon"><svg width="11" height="11" viewBox="0 0 12 12"><rect x="1" y="2.5" width="10" height="7" fill="#fff"/><path d="M1 3l5 4 5-4" stroke="var(--red)" fill="none"/></svg></i>info@marigoldswim.org</span>
    <span class="signup-btn">✎ SIGN UP</span>
  </div>
  <nav class="abs nav" style="top:56px">
    <span class="active">HOME</span><span>ABOUT US</span><span>SERVICES</span><span>SPECIAL EVENTS</span><span>SHOP</span><span>SPONSOR</span><span>CONTACT US</span>
  </nav>
  <svg class="abs search" style="top:58px" width="16" height="16" viewBox="0 0 16 16"><circle cx="6.5" cy="6.5" r="5" stroke="#222" stroke-width="2" fill="none"/><path d="M10.5 10.5 15 15" stroke="#222" stroke-width="2"/></svg>
</header>
<div class="abs logo-disc"><span class="logo-mark"></span><span class="logo-name">MARIGOLD</span></div>

<!-- registration steps -->
<section class="abs steps">
  <h2 class="heading">MULTI STEP REGISTRATION PROCESS</h2>
  <p class="steps-intro">Nam libero tempore, cum soluta nobis est eligendi optio cumque nihil impedit quo minus id quod maxime placeat facere possimus, omnis voluptas assumenda est, omnis dolor repellendus temporibus autem quibusdam et aut officiis debitis aut rerum necessitatibus saepe eveniet.</p>

  <div class="step" style="left:91px">
    <div class="step-ring"><svg width="50" height="38" viewBox="0 0 50 38"><rect x="1" y="1" width="48" height="36" rx="4" fill="var(--aqua)"/><rect x="1" y="8" width="48" height="7" fill="#fff"/><rect x="7" y="24" width="14" height="4" fill="#fff"/></svg></div>
    <div class="step-name">Pay Fees</div>
    <p class="step-text">Nam libero tempore, cum soluta nobis est eligendi optio cumque nihil impe dit quo minus quod max</p>
  </div>
  <div class="step" style="left:351px">
    <div class="step-ring"><svg width="50" height="44" viewBox="0 0 50 44"><path d="M2 2v40h46" stroke="var(--aqua)" stroke-width="3" fill="none"/><rect x="10" y="22" width="7" height="18" fill="var(--aqua)"/><rect x="21" y="12" width="7" height="28" fill="var(--aqua)"/><rect x="32" y="18" width="7" height="22" fill="var(--aqua)"/></svg></div>
    <div class="step-name">Sign Waivers</div>
    <p class="step-text">Nam libero tempore, cum soluta nobis est eligendi optio cumque nihil impe dit quo minus quod max</p>
  </div>
  <div class="step" style="left:612px">
    <div class="step-ring"><svg width="50" height="50" viewBox="0 0 50 50"><circle cx="25" cy="25" r="23" fill="var(--aqua)"/><path d="M14 26l8 8 15-16" stroke="#fff" stroke-width="5" fill="none"/></svg></div>
    <div class="step-name">Reserve a Spot</div>
    <p class="step-text">Nam libero tempore, cum soluta nobis est eligendi optio cumque nihil impe dit quo minus quod max</p>
  </div>
  <div class="step" style="left:872px">
    <div class="step-ring"><svg width="58" height="44" viewBox="0 0 58 44"><circle cx="29" cy="12" r="9" fill="var(--aqua)"/><path d="M14 42c0-12 7-18 15-18s15 6 15 18z" fill="var(--aqua)"/><circle cx="11" cy="16" r="6" fill="var(--aqua)"/><circle cx="47" cy="16" r="6" fill="var(--aqua)"/><path d="M0 38c0-8 5-13 11-13 3 0 5 1 6 2-3 3-4 7-4 11z M58 38c0-8-5-13-11-13-3 0-5 1-6 2 3 3 4 7 4 11z" fill="var(--aqua)"/></svg></div>
    <div class="step-name">Buy National Membership</div>
    <p class="step-text">Nam libero tempore, cum soluta nobis est eligendi optio cumque nihil impe dit quo minus quod max</p>
  </div>

  <svg class="step-arrow" style="left:290px" width="82" height="40" viewBox="0 0 82 40"><path d="M4 6c30 0 50 10 68 26" stroke="#aaa" stroke-width="2" fill="none"/><path d="M62 32h12V20" stroke="#aaa" stroke-width="2" fill="none"/></svg>
  <svg class="step-arrow" style="left:552px" width="82" height="40" viewBox="0 0 82 40"><path d="M4 34c28 0 48-10 66-26" stroke="#aaa" stroke-width="2" fill="none"/><path d="M60 6h12v12" stroke="#aaa" stroke-width="2" fill="none"/></svg>
  <svg class="step-arrow" style="left:812px" width="82" height="40" viewBox="0 0 82 40"><path d="M4 6c30 0 50 10 68 26" stroke="#aaa" stroke-width="2" fill="none"/><path d="M62 32h12V20" stroke="#aaa" stroke-width="2" fill="none"/></svg>
</section>
<div class="abs divider" style="top:1207px"></div>

<!-- special events -->
<h2 class="abs heading events-title">SPECIAL EVENTS</h2>

<article class="abs event" style="top:1322px"><div class="event-photo photo" role="img" aria-label="Swimmers performing a routine in the pool"></div><div class="event-body"><h3 class="event-title">Smilique sunt in culpa qui officia deserunt</h3><div class="meta"><i></i>Jul 29, 2016 | <i></i>John | <i></i>0 Comments</div><p class="event-text">At vero eos et accusamus et iusto odio dignissimos ducimus blanditiis praesentium voluptatum deleniti atque corrupti quo os dolores et quas molestias excepturi</p><p class="more" style="margin-top:12px">READ MORE &gt;&gt;</p></div></article>
<article class="abs event" style="top:1549px"><div class="event-photo photo" role="img" aria-label="Team in red suits posing in a circle formation"></div><div class="event-body"><h3 class="event-title">Smilique sunt in culpa qui officia deserunt</h3><div class="meta"><i></i>Jul 29, 2016 | <i></i>John | <i></i>0 Comments</div><p class="event-text">At vero eos et accusamus et iusto odio dignissimos ducimus blanditiis praesentium voluptatum deleniti atque corrupti quo os dolores et quas molestias excepturi</p><p class="more" style="margin-top:12px">READ MORE &gt;&gt;</p></div></article>
<article class="abs event" style="top:1776px"><div class="event-photo photo" role="img" aria-label="Swimmer floating on her back in clear water"></div><div class="event-body"><h3 class="event-title">Smilique sunt in culpa qui officia deserunt</h3><div class="meta"><i></i>Jul 29, 2016 | <i></i>John | <i></i>0 Comments</div><p class="event-text">At vero eos et accusamus et iusto odio dignissimos ducimus blanditiis praesentium voluptatum deleniti atque corrupti quo os dolores et quas molestias excepturi</p><p class="more" style="margin-top:12px">READ MORE &gt;&gt;</p></div></article>
<article class="abs event" style="top:2003px"><div class="event-photo photo" role="img" aria-label="Swimmer in red cap mid stroke"></div><div class="event-body"><h3 class="event-title">Smilique sunt in culpa qui officia deserunt</h3><div class="meta"><i></i>Jul 29, 2016 | <i></i>John | <i></i>0 Comments</div><p class="event-text">At vero eos et accusamus et iusto odio dignissimos ducimus blanditiis praesentium voluptatum deleniti atque corrupti quo os dolores et quas molestias excepturi</p><p class="more" style="margin-top:12px">READ MORE &gt;&gt;</p></div></article>
<article class="abs event" style="top:2230px;border-bottom:none"><div class="event-photo photo" role="img" aria-label="Pair of swimmers practising a lift"></div><div class="event-body"><h3 class="event-title">Smilique sunt in culpa qui officia deserunt</h3><div class="meta"><i></i>Jul 29, 2016 | <i></i>John | <i></i>0 Comments</div><p class="event-text">At vero eos et accusamus et iusto odio dignissimos ducimus blanditiis praesentium voluptatum deleniti atque corrupti quo os dolores et quas molestias excepturi</p><p class="more" style="margin-top:12px">READ MORE &gt;&gt;</p></div></article>
<p class="abs more" style="left:98px;top:2448px">VIEW MORE &gt;&gt;</p>

<!-- calendar -->
<h2 class="abs heading cal-title">TEAM CALENDAR</h2>
<div class="abs calendar">
  <div class="cal-head"><span>◀</span><span>DEC 2016</span><span>▶</span></div>
  <div class="cal-grid">
    <b>Su</b><b>Mo</b><b>Tu</b><b>We</b><b>Th</b><b>Fr</b><b>Sa</b>
    <span class="empty"></span><span class="empty"></span><span class="empty"></span><span>1</span><span class="today">2</span><span>3</span><span>4</span>
    <span>5</span><span>6</span><span>7</span><span>8</span><span>9</span><span>10</span><span>11</span>
    <span>12</span><span>13</span><span>14</span><span>15</span><span>16</span><span>17</span><span>18</span>
    <span>19</span><span>20</span><span>21</span><span>22</span><span>23</span><span>24</span><span>25</span>
    <span>26</span><span>27</span><span>28</span><span>29</span><span>30</span><span>31</span><span class="empty"></span>
  </div>
</div>

<!-- news -->
<h2 class="abs heading news-title">NEWS</h2>
<div class="abs news-item" style="top:1740px"><div class="news-thumb photo" role="img" aria-label="Team group on pool deck"></div><div><h3 class="news-name">Finibus Bonorum et Malorum</h3><div class="meta"><i></i>Jul 29, 2016 | <i></i>John</div></div></div>
<div class="abs news-item" style="top:1839px"><div class="news-thumb photo" role="img" aria-label="Swimmers training in the pool"></div><div><h3 class="news-name">Finibus Bonorum et Malorum</h3><div class="meta"><i></i>Jul 29, 2016 | <i></i>John</div></div></div>
<div class="abs news-item" style="top:1938px"><div class="news-thumb" style="background:linear-gradient(135deg,#d9b7a3,#8c6f63)" role="img" aria-label="Young swimmers at a meet"></div><div><h3 class="news-name">Finibus Bonorum et Malorum</h3><div class="meta"><i></i>Jul 29, 2016 | <i></i>John</div></div></div>
<div class="abs news-item" style="top:2037px;border-bottom:none"><div class="news-thumb" style="background:linear-gradient(135deg,#e7b54b,#c2412c)" role="img" aria-label="Team celebration with gifts"></div><div><h3 class="news-name">Finibus Bonorum et Malorum</h3><div class="meta"><i></i>Jul 29, 2016 | <i></i>John</div></div></div>
<p class="abs more" style="left:764px;top:2141px">VIEW MORE &gt;&gt;</p>

<!-- video -->
<h2 class="abs heading video-title">VIDEO</h2>
<div class="abs video photo" role="img" aria-label="Video of a synchronized swim routine">
  <span class="play"><svg width="18" height="20" viewBox="0 0 18 20"><path d="M2 1l15 9-15 9z" fill="#fff"/></svg></span>
</div>
<div class="abs divider" style="top:2508px"></div>

<!-- photos -->
<h2 class="abs heading photos-title">PHOTOS</h2>
<div class="abs photo-grid">
  <div class="photo" role="img" aria-label="Swimmer's arm rising from water"></div>
  <div style="background:linear-gradient(135deg,#7ec07a,#e3c046)" role="img" aria-label="Swimmer poised by the pool"></div>
  <div style="background:linear-gradient(135deg,#bfc7cf,#5d89a6)" role="img" aria-label="Team members on deck"></div>
  <div class="photo" role="img" aria-label="Swimmers in formation"></div>
  <div class="photo" role="img" aria-label="Swimmer mid stroke"></div>
  <div style="background:linear-gradient(135deg,#9fd3e0,#4f8fb0)" role="img" aria-label="Pool lanes during practice"></div>
  <div style="background:linear-gradient(135deg,#e8e8e8,#b3b3b3)" role="img" aria-label="Swim team sketch"></div>
  <div style="background:linear-gradient(135deg,#d9b7a3,#7c6a62)" role="img" aria-label="Two young swimmers"></div>
</div>

<!-- social feed -->
<h2 class="abs heading feed-title">FRIENDBOOK FEED</h2>
<div class="abs feed">
  <div class="feed-cover" role="img" aria-label="Team page cover photo of pool">
    <span class="feed-avatar"></span>
    <span class="feed-name">MARIGOLD LLC</span>
    <span class="feed-sub">1,235 likes</span>
    <span class="feed-btn" style="left:12px">Like Page</span>
    <span class="feed-btn" style="right:12px">✎ Sign Up</span>
  </div>
  <p class="feed-note">Be the first of your friends to like this</p>
  <div class="feed-faces"><span></span><span></span><span></span><span></span><span></span><span></span><span></span></div>
</div>

<!-- sponsors -->
<section class="abs sponsors">
  <h2 class="heading">OUR SPONSORS</h2>
  <svg class="abs sponsor-arrow" style="left:84px" width="16" height="24" viewBox="0 0 16 24"><path d="M13 2 3 12l10 10" stroke="#777" stroke-width="2.5" fill="none"/></svg>
  <div class="sponsor-row">
    <div class="sponsor"><i></i></div><div class="sponsor"><i></i></div><div class="sponsor"><i></i></div><div class="sponsor"><i></i></div><div class="sponsor"><i></i></div>
  </div>
  <svg class="abs sponsor-arrow" style="left:1098px" width="16" height="24" viewBox="0 0 16 24"><path d="M3 2l10 10L3 22" stroke="#777" stroke-width="2.5" fill="none"/></svg>
</section>

<!-- footer -->
<svg class="abs footer-wave" width="1200" height="52" viewBox="0 0 1200 52"><path d="M0 20 C300 60 700 -10 1200 30 L1200 52 L0 52Z" fill="var(--aqua)"/><path d="M0 38 C320 62 760 10 1200 42 L1200 52 L0 52Z" fill="var(--footer)"/></svg>
<footer class="abs footer">
  <div class="f-col" style="left:98px"><h4>Information</h4><ul><li>About Us</li><li>Careers</li><li>Privacy &amp; Security</li><li>Site Map</li><li>Terms of Use</li><li>Blog</li></ul></div>
  <div class="f-col" style="left:295px"><h4>Help &amp; support</h4><ul><li>Rashguards</li><li>Boardshorts</li><li>Wetsuits</li><li>Kids Swimwear</li><li>Plus Size Swimwear</li><li>Swim Parkas</li></ul></div>
  <div class="f-col" style="left:509px;width:240px"><h4>Contact Us</h4>
    <div class="f-contact"><svg width="12" height="16" viewBox="0 0 12 16"><path d="M6 0a6 6 0 0 0-6 6c0 4 6 10 6 10s6-6 6-10a6 6 0 0 0-6-6z" fill="#fff"/><circle cx="6" cy="6" r="2" fill="var(--footer)"/></svg><span>At vero eos et accusamus et iusto odio dignissimos ducimus qui</span></div>
    <div class="f-contact"><svg width="14" height="14" viewBox="0 0 12 12"><path d="M2 1h3l1 3-2 1a7 7 0 0 0 3 3l1-2 3 1v3c-6 0-10-4-9-9z" fill="#fff"/></svg><span>1-888-888-8888</span></div>
    <div class="f-contact"><svg width="14" height="12" viewBox="0 0 14 12"><rect x="0" y="1" width="14" height="10" fill="#fff"/><path d="M0 2l7 5 7-5" stroke="var(--footer)" fill="none"/></svg><span>info@marigoldswim.org</span></div>
  </div>
  <div class="f-col" style="left:778px;width:324px"><h4>Email Subscription</h4>
    <p style="font-size:13px">Register your email address to get information about us</p>
    <div class="subscribe"><span>Email Address</span><b>SUBSCRIBE</b></div>
    <h4 style="margin-top:20px;margin-bottom:0">Stay Connected</h4>
    <div class="socials"><span></span><span></span><span></span><span></span><span></span><span></span><span></span><span></span><span></span></div>
  </div>
  <p class="copyright">Copyrights © 2016 Marigold Inc. All Rights Reserved &nbsp;|&nbsp; Privacy Policy &nbsp;|&nbsp; Terms of Use &nbsp;|&nbsp; Feedback</p>
</footer>

<!-- age verification modal -->
<div class="abs dim"></div>
<div class="abs modal" role="dialog" aria-label="Age verification">
  <span class="modal-close">X</span>
  <div class="modal-brand"><span class="logo-mark"></span><span class="logo-name" style="font-size:18px">MARIGOLD</span></div>
  <h2 class="modal-title">AGE VERIFICATION</h2>
  <p class="modal-text">At vero eos et accusamus et iusto odio dignissimos ducimus qui blanditiis praesentium voluptatum deleniti atque corrupti quos dolores et quas molestias excepturi sint occaecati cupiditate milique sunt in culpa deser qui off</p>
  <div class="modal-actions"><span class="btn-youth">FOR YOUTH</span><span class="btn-adult">FOR ADULT</span></div>
</div>

</body>
</html>
```